Tour poster for outback tour company

We need an eye-catching but classy poster for our tour business.

We are open to design ideas but were thinking some sort of a collage with some of the pictures.

We would like to add two itineraries to the poster.
“The Premium Tour” ($110)
- Jed’s Digging Shaft
- The Kestrel Chapel (Underground) Hall
- The Wombat Barrier
- The Ember Flats
- The Redfalls
- A visit to our private claim in the opal fields
- Complimentary glass of sparkling wine/lemonade at The Redfalls

“Under the Crust: Marla Vale Starter Tour”
($75)

Karinda Gem Pit and Gallery
- Award-winning movie
- Underground Houses
- Underground Mine Tour

Kestrel Chapel Hall
Saddle Ridge Graveyard
Scenic Drive Around Town

Can we also add somewhere “As featured on shows such as ‘The Sunny Side Household’ and ‘Outback Roads with Rhys’”

The poster will also need to include our contact details.
Phone number: 0412 738 615
Website: dustrovertrips.example.com.au
E-mail: dustrovertrips@mailbox.example

Industry/Entity Type

Tourism

Font styles to use
Serif

Colors
FFF300
FFF600
FEFA6F
FFFEC7
FFFEE8
FFC000
F8CF3A
FAE287
FDF2CF
FEFAEE
F0912C
F2A743
F7CA91
FBE8D2
FDF5EE
EE7325
F08F49
F5BC92
FAE3D3
FDF4ED
EB3D1F
EC4F4E
F09395
F8D3D4
FCEDEE

Requirements
Must have
• Dustrover Trips logo and JourneyRater logo

```html
<!DOCTYPE html>
<html lang="en">
<head>
<meta charset="UTF-8">
<title>Dustrover Trips – Tour Poster</title>
<link rel="stylesheet" href="https://fonts.googleapis.com/css2?family=Cinzel:wght@600;700;800&family=Roboto:wght@400&display=swap">
<style>
  :root {
    --poster-bg: #161414;
    --ink-light: #fffee8;
    --cream: #fdf2cf;
    --orange: #ee7325;
    --orange-soft: #f08f49;
    --red: #eb3d1f;
    --deep-red: #7a1a0e;
    --rust: #a8330f;
    --gold: #ffc000;
    --white-box: #f4f4f4;
    --badge: #1fbfb0;
    --dark-text: #161414;
  }
  * { box-sizing: border-box; margin: 0; padding: 0; }
  html, body { width: 960px; height: 1200px; overflow: hidden; background: var(--poster-bg); }
  .poster {
    position: relative; width: 960px; height: 1200px;
    background: var(--poster-bg); font-family: "Cinzel", Georgia, serif; color: var(--ink-light);
  }

  /* Hero */
  .hero {
    position: absolute; left: 22px; top: 22px; width: 916px; height: 450px;
    border-radius: 18px; overflow: hidden;
    background:
      radial-gradient(circle at 70% 26%, #fff0c4 0%, #ffc36a 6%, rgba(245,150,60,0) 22%),
      radial-gradient(ellipse 60% 80% at 62% 45%, #f5a04a 0%, #de6e22 35%, rgba(160,60,16,0) 75%),
      linear-gradient(120deg, #6e240a 0%, #b8481a 35%, #c85a1e 60%, #7c2c0c 100%);
    box-shadow: inset 0 0 80px rgba(40,10,0,0.55);
  }
  .brand {
    position: absolute; left: 0; right: 0; top: 150px;
    display: flex; justify-content: center; align-items: center; gap: 24px;
  }
  .brand-mark { width: 54px; height: 54px; background: var(--cream); border-radius: 6px; }
  .brand-text { display: flex; flex-direction: column; align-items: center; color: var(--cream); font-weight: 800; line-height: 1; }
  .brand-name { font-size: 72px; letter-spacing: 1px; }
  .brand-region { font-size: 44px; letter-spacing: 30px; margin-top: 18px; margin-right: -30px; }

  /* Collage */
  .collage { position: absolute; left: 22px; top: 486px; width: 916px; height: 330px; }
  .photo { position: absolute; box-shadow: inset 0 0 40px rgba(0,0,0,0.35); }
  .photo-mine { left: 0; top: 0; width: 256px; height: 158px;
    background: radial-gradient(circle at 75% 60%, #d9a44c 0%, rgba(160,120,80,0) 30%), linear-gradient(135deg, #b8a284 0%, #8a7458 50%, #4e3e2e 100%); }
  .photo-lookout { left: 0; top: 168px; width: 256px; height: 162px;
    background: linear-gradient(180deg, #c9d3db 0%, #e0c9a6 22%, #c77a48 40%, #a0492a 65%, #5a3424 100%); }
  .photo-chapel { left: 266px; top: 0; width: 380px; height: 330px;
    background: radial-gradient(ellipse 40% 30% at 50% 22%, #f3e6c4 0%, rgba(210,190,150,0) 100%), linear-gradient(180deg, #d6c7a8 0%, #b89468 35%, #7c3f1e 60%, #4c2210 85%, #a89478 100%); }
  .photo-vehicle { left: 656px; top: 0; width: 260px; height: 158px;
    background: linear-gradient(180deg, #2f6fd0 0%, #79a8e2 28%, #b88a62 42%, #c9a888 70%, #d8c0a4 100%); }
  .photo-walkers { left: 656px; top: 168px; width: 260px; height: 162px;
    background: linear-gradient(180deg, #d08a5a 0%, #c06a3a 40%, #b45a30 70%, #9c4a26 100%); }

  /* Tours */
  .tour { position: absolute; top: 834px; }
  .tour-premium { left: 22px; width: 452px; }
  .tour-starter { left: 488px; width: 450px; }
  .tour-head { display: flex; height: 54px; border-radius: 6px; overflow: hidden; }
  .tour-title {
    flex: 1; display: flex; flex-direction: column; justify-content: center; padding-left: 14px;
    background: linear-gradient(90deg, var(--deep-red), var(--orange));
    font-weight: 700; font-size: 25px; color: var(--ink-light); font-variant: small-caps; line-height: 1;
  }
  .tour-title small { font-size: 13px; font-weight: 700; margin-top: 2px; }
  .tour-price {
    width: 108px; display: flex; align-items: center; justify-content: center;
    background: var(--white-box); color: var(--dark-text); font-weight: 700; font-size: 26px;
  }
  .stops { display: grid; grid-template-columns: 1fr 1fr; column-gap: 10px; margin-top: 14px; }
  .stop-list { list-style: none; }
  .stop {
    display: flex; gap: 8px; align-items: flex-start;
    font-size: 13px; font-weight: 700; font-variant: small-caps; line-height: 1.2; margin-bottom: 13px;
  }
  .stop svg { flex: none; width: 17px; height: 17px; margin-top: -1px; }
  .stop-red svg { color: var(--rust); }
  .stop-orange svg { color: var(--orange); }
  .stop-notes {
    display: flex; gap: 6px; font-family: "Roboto", Arial, sans-serif; font-size: 9.5px;
    margin: -8px 0 14px 20px; text-align: center; line-height: 1.2;
  }
  .stop-notes span + span { border-left: 1px solid var(--orange); padding-left: 6px; }

  /* Featured */
  .featured { position: absolute; left: 22px; top: 1054px; width: 916px; height: 38px; display: flex; }
  .featured-label {
    width: 440px; display: flex; align-items: center; padding-left: 14px;
    background: linear-gradient(90deg, var(--deep-red), var(--orange));
    font-weight: 700; font-size: 21px; font-variant: small-caps;
  }
  .featured-shows {
    flex: 1; display: flex; align-items: center; justify-content: space-around;
    background: var(--white-box); color: var(--dark-text);
    font-family: "Roboto", Arial, sans-serif; font-size: 17px;
  }
  .featured-shows .divider { width: 2px; height: 18px; background: var(--orange); }

  /* Contact */
  .contact { position: absolute; left: 22px; top: 1110px; width: 916px; height: 62px; display: flex; align-items: center; gap: 18px; }
  .contact-phone {
    display: flex; align-items: center; gap: 12px; height: 52px; padding: 0 16px;
    background: linear-gradient(90deg, var(--deep-red), var(--rust)); border-radius: 4px;
    font-family: "Roboto", Arial, sans-serif; font-size: 26px; color: var(--cream);
  }
  .contact-item { display: flex; align-items: center; gap: 8px; font-family: "Roboto", Arial, sans-serif; font-size: 17px; }
  .contact-item svg, .contact-phone svg { flex: none; }
  .rating-badge { margin-left: auto; width: 58px; height: 58px; background: var(--badge); border-radius: 3px; }
</style>
</head>
<body>
<svg width="0" height="0" style="position:absolute" aria-hidden="true">
  <symbol id="sun" viewBox="0 0 16 16">
    <circle cx="8" cy="8" r="3.4" fill="currentColor"/>
    <g stroke="currentColor" stroke-width="1.4" stroke-linecap="round">
      <line x1="8" y1="0.8" x2="8" y2="2.6"/><line x1="8" y1="13.4" x2="8" y2="15.2"/>
      <line x1="0.8" y1="8" x2="2.6" y2="8"/><line x1="13.4" y1="8" x2="15.2" y2="8"/>
      <line x1="2.9" y1="2.9" x2="4.2" y2="4.2"/><line x1="11.8" y1="11.8" x2="13.1" y2="13.1"/>
      <line x1="2.9" y1="13.1" x2="4.2" y2="11.8"/><line x1="11.8" y1="4.2" x2="13.1" y2="2.9"/>
    </g>
  </symbol>
</svg>

<main class="poster">
  <section class="hero" role="img" aria-label="Glowing orange underground mine tunnel carved in sandstone, lit opening at the far end">
    <div class="brand">
      <span class="brand-mark"></span>
      <div class="brand-text">
        <span class="brand-name">Dustrover Trips</span>
        <span class="brand-region">AUSTRALIA</span>
      </div>
    </div>
  </section>

  <section class="collage">
    <div class="photo photo-mine" role="img" aria-label="Underground dugout with a miner statue and gated tunnel entrance"></div>
    <div class="photo photo-lookout" role="img" aria-label="Visitor sitting on a lookout over colourful desert mesas at dusk"></div>
    <div class="photo photo-chapel" role="img" aria-label="Carved sandstone altar wall with painted icon screen inside the underground chapel"></div>
    <div class="photo photo-vehicle" role="img" aria-label="Tour four-wheel-drive parked by dugout entrances under blue sky"></div>
    <div class="photo photo-walkers" role="img" aria-label="Small group walking across red desert plains toward the tour vehicle"></div>
  </section>

  <section class="tour tour-premium">
    <header class="tour-head">
      <h2 class="tour-title">The Premium Tour</h2>
      <div class="tour-price">($110)</div>
    </header>
    <div class="stops">
      <ul class="stop-list">
        <li class="stop stop-red"><svg><use href="#sun"/></svg>Jed’s Digging Shaft</li>
        <li class="stop stop-red"><svg><use href="#sun"/></svg>The Kestrel Chapel (Underground) Hall</li>
        <li class="stop stop-red"><svg><use href="#sun"/></svg>The Wombat Barrier</li>
        <li class="stop stop-red"><svg><use href="#sun"/></svg>The Ember Flats</li>
      </ul>
      <ul class="stop-list">
        <li class="stop stop-orange"><svg><use href="#sun"/></svg>The Redfalls</li>
        <li class="stop stop-orange"><svg><use href="#sun"/></svg>A visit to our private claim in the opal fields</li>
        <li class="stop stop-orange"><svg><use href="#sun"/></svg>Complimentary glass of sparkling wine/lemonade at The Redfalls</li>
      </ul>
    </div>
  </section>

  <section class="tour tour-starter">
    <header class="tour-head">
      <h2 class="tour-title">Under the Crust:<small>Marla Vale Starter Tour</small></h2>
      <div class="tour-price">($75)</div>
    </header>
    <div class="stops">
      <div>
        <ul class="stop-list">
          <li class="stop stop-orange"><svg><use href="#sun"/></svg>Karinda Gem Pit and Gallery</li>
        </ul>
        <div class="stop-notes">
          <span>Award-winning<br>movie</span>
          <span>Underground<br>Houses</span>
          <span>Underground<br>Mine Tour</span>
        </div>
        <ul class="stop-list">
          <li class="stop stop-orange"><svg><use href="#sun"/></svg>Saddle Ridge Graveyard</li>
        </ul>
      </div>
      <ul class="stop-list">
        <li class="stop stop-orange"><svg><use href="#sun"/></svg>Kestrel Chapel Hall</li>
        <li class="stop stop-orange" style="margin-top:30px"><svg><use href="#sun"/></svg>Scenic Drive Around Town</li>
      </ul>
    </div>
  </section>

  <section class="featured">
    <div class="featured-label">As featured on shows such as</div>
    <div class="featured-shows">
      <span>The Sunny Side Household</span>
      <span class="divider"></span>
      <span>Outback Roads with Rhys</span>
    </div>
  </section>

  <footer class="contact">
    <div class="contact-phone">
      <svg width="22" height="22" viewBox="0 0 22 22" aria-hidden="true">
        <circle cx="11" cy="11" r="11" fill="#fdf2cf"/>
        <path d="M7.5 5.5l2 0 1 3-1.3 1c.7 1.5 1.8 2.6 3.3 3.3l1-1.3 3 1v2c0 .6-.5 1-1 1C10.3 15.5 6.5 11.7 6.5 6.5c0-.5.4-1 1-1z" fill="#7a1a0e"/>
      </svg>
      0412 738 615
    </div>
    <div class="contact-item">
      <svg width="20" height="20" viewBox="0 0 20 20" aria-hidden="true">
        <circle cx="10" cy="10" r="10" fill="#ee7325"/>
        <rect x="5" y="6.5" width="10" height="7" rx="1" fill="#161414"/>
        <path d="M5.5 7l4.5 3.5L14.5 7" stroke="#ee7325" stroke-width="1.2" fill="none"/>
      </svg>
      dustrovertrips@mailbox.example
    </div>
    <div class="contact-item">
      <svg width="20" height="20" viewBox="0 0 20 20" aria-hidden="true">
        <circle cx="10" cy="10" r="9" fill="none" stroke="#ee7325" stroke-width="2"/>
        <ellipse cx="10" cy="10" rx="4" ry="9" fill="none" stroke="#ee7325" stroke-width="1.6"/>
        <line x1="1" y1="10" x2="19" y2="10" stroke="#ee7325" stroke-width="1.6"/>
      </svg>
      dustrovertrips.example.com.au
    </div>
    <div class="rating-badge" role="img" aria-label="JourneyRater award badge"></div>
  </footer>
</main>
</body>
</html>
```